Web Design Project

Crest Tide needs a new web page design.

This final product MUST be a layered .psd format for our CSS coder to do properly.

What we need is a 3 column template similar to the attached sample. We NEED to have 3 defined sections "Learn" "Shop" and "Dive." This is very important.

Our store font is Ethnocentric, so any design which incorporates this somehow would be great. Our logo is attached in a .jpeg and .psd format. Feel free to manipulate the logo background into a design that works.

Preferred colors are blue (not light blue,) grey, black and yellow. The center section of the template must remain white.

Crest Tide is a website for technical and rebreather equipment, and training. PLEASE do NOT show images of recreational scuba divers. This is not our market and designs featuring recreational 'touristy' divers will be eliminated.

Attached are logos, and images for use as a background image.

Target Market(s)

Males 25-60

Industry/Entity Type

Store

Requirements
Must have
• - 3 defined sections "Learn" "Shop" "Dive"
- White center area
- Final format must be delivered in a layered .psd file for our CSS coder to cut
Nice to have
• -Ethnocentric fonts
-3d borders
-Textures
- Blue, great black, yellow colors.
- Simple, uncluttered design
Should not have
• Images or logos of recreational or 'tourist' scuba divers. This is a technical and rebreather diving business.

Light blue colors

```html
<!DOCTYPE html>
<html lang="en">
<head>
<meta charset="utf-8">
<title>Crest Tide Store</title>
<link rel="stylesheet" href="https://fonts.googleapis.com/css2?family=Orbitron:wght@500;700;900&family=Exo+2:ital,wght@1,800&family=Arimo:wght@400;700&display=swap">
<style>
:root{
  --deep:#06162f;
  --ocean:#0d3470;
  --ocean-mid:#1a4f96;
  --tab:#0b3f86;
  --tab-edge:#3d72bd;
  --bar:#1b1b1d;
  --panel:#ffffff;
  --side:#f6f7f9;
  --ink:#1a1a1a;
  --muted:#333;
  --link:#7a1f3a;
  --pale:#dfe9f7;
}
*{margin:0;padding:0;box-sizing:border-box}
html,body{width:1200px;height:710px;overflow:hidden}
body{font-family:"Arimo",Arial,sans-serif;color:var(--ink);background:var(--deep);position:relative}
.backdrop{position:absolute;inset:0;background:
  radial-gradient(ellipse 22% 30% at 6% 30%,#2b64ac88 0%,transparent 70%),
  radial-gradient(ellipse 22% 30% at 94% 30%,#2b64ac88 0%,transparent 70%),
  radial-gradient(ellipse 60% 40% at 50% 8%,#2a63ad 0%,transparent 70%),
  linear-gradient(180deg,var(--ocean-mid) 0%,var(--ocean) 35%,var(--deep) 100%)}
.abs{position:absolute}
.brand{left:192px;top:22px;width:185px;height:80px;display:flex;align-items:center;gap:10px}
.brand-dot{width:26px;height:26px;border-radius:50%;background:var(--pale)}
.brand-name{font-family:"Orbitron",sans-serif;font-weight:900;font-size:23px;color:var(--pale);letter-spacing:1px;line-height:1.05}
.call{left:454px;top:26px;font-family:"Orbitron",sans-serif;font-weight:500;font-size:13px;color:#eef3fb;line-height:17px;letter-spacing:.5px}
.search{left:448px;top:60px;width:188px;height:22px;border-radius:11px;background:linear-gradient(#0c2c5d,#1b4483);box-shadow:inset 0 1px 3px #000a}
.search-go{position:absolute;right:2px;top:2px;width:38px;height:18px;border-radius:9px;background:linear-gradient(#5b86c4,#2b5699);font-family:"Orbitron",sans-serif;font-size:11px;color:#fff;text-align:center;line-height:18px}
.topnav{left:560px;top:0;width:445px;height:27px;background:linear-gradient(#2155a0,#0d3470);border-radius:0 0 14px 14px;border:1px solid var(--tab-edge);border-top:0;display:flex;justify-content:space-around;align-items:center;font-size:11px;color:#fff;padding:0 14px}
.topnav span{display:flex;align-items:center;gap:5px}
.ship{left:790px;top:48px;width:200px;text-align:center;color:#fff;font-family:"Orbitron",sans-serif}
.ship b{display:block;font-size:19px;font-weight:700;letter-spacing:1.5px}
.ship small{display:block;font-size:12px;letter-spacing:1px}
.intl{left:248px;top:122px;font-family:"Orbitron",sans-serif;font-size:13px;color:#dfe9f7;letter-spacing:.6px}
.tabbar{left:633px;top:109px;width:378px;height:35px;background:var(--bar);clip-path:polygon(18px 0,100% 0,100% 100%,0 100%);display:flex;justify-content:space-around;align-items:center;padding-left:18px;font-family:"Exo 2",sans-serif;font-style:italic;font-weight:800;font-size:14px;color:#fff;letter-spacing:.5px}
.panel{left:190px;top:142px;width:821px;height:512px;background:var(--panel);border-radius:0 0 8px 8px;overflow:hidden}
.col-side{position:absolute;top:0;bottom:0;background:var(--side)}
.col-left{left:0;width:193px;box-shadow:3px 0 6px #0002}
.col-right{right:0;width:194px;box-shadow:-3px 0 6px #0002}
.head{position:absolute;top:9px;height:28px;background:linear-gradient(#1b58a8,var(--tab));clip-path:polygon(10px 0,100% 0,calc(100% - 10px) 100%,0 100%);font-family:"Exo 2",sans-serif;font-style:italic;font-weight:800;font-size:16px;color:#fff;letter-spacing:1.5px;text-align:center;line-height:28px}
.story{position:absolute;left:10px;width:174px;font-size:9.5px;line-height:12.5px;color:var(--muted)}
.story h3{font-size:11.5px;font-weight:700;color:var(--ink);text-align:center;margin-bottom:4px}
.photo{height:108px;margin-bottom:8px}
.photo-video{background:
  radial-gradient(ellipse 30% 55% at 22% 60%,#3b3330 0%,transparent 70%),
  linear-gradient(100deg,#c9b7a1 0%,#9a8f7e 35%,#6f8a8c 60%,#d6cdb8 100%)}
.photo-shop{background:
  radial-gradient(ellipse 35% 50% at 50% 60%,#5a4c40 0%,transparent 70%),
  linear-gradient(180deg,#d9d4c6 0%,#a69d8c 50%,#3f3833 100%)}
.more{display:block;text-align:right;color:var(--link);margin-top:3px}
.product{position:absolute;width:117px}
.product-img{height:114px;border:1px solid #222;background:#fff}
.product-name{margin-top:6px;text-align:center;font-family:"Orbitron",sans-serif;font-size:9px;letter-spacing:.6px;color:#333;white-space:nowrap}
.tile-wings{background:radial-gradient(ellipse 30% 45% at 30% 50%,#2a0d10 0%,#7d1a20 45%,transparent 75%),radial-gradient(ellipse 28% 48% at 72% 48%,#4a4d52 0%,#a9adb2 55%,transparent 80%),#fff}
.tile-computers{background:radial-gradient(ellipse 35% 38% at 35% 35%,#3b5b3c 0%,#2b2f33 50%,transparent 75%),radial-gradient(ellipse 30% 32% at 68% 70%,#23405f 0%,#1d1f22 55%,transparent 80%),#fff}
.tile-handsets{background:radial-gradient(ellipse 40% 28% at 40% 78%,#1a1a1a 0%,#3a3a3a 55%,transparent 80%),radial-gradient(ellipse 14% 30% at 70% 38%,#e24a1d 0%,#f07a3d 60%,transparent 85%),radial-gradient(ellipse 22% 22% at 35% 18%,#222 0%,transparent 80%),#fff}
.tile-cylinders{background:radial-gradient(ellipse 40% 45% at 35% 58%,#c9cdd1 0%,#8f959b 55%,transparent 80%),radial-gradient(ellipse 12% 45% at 80% 55%,#3b3d40 0%,transparent 80%),#fff}
.tile-hardware{background:radial-gradient(ellipse 32% 28% at 35% 25%,#a8acb0 0%,#d4d7da 60%,transparent 85%),radial-gradient(ellipse 25% 18% at 25% 80%,#3d2a1c 0%,transparent 80%),radial-gradient(ellipse 18% 32% at 72% 68%,#9ea3a8 0%,transparent 80%),#fff}
.tile-lights{background:radial-gradient(ellipse 30% 16% at 25% 33%,#151515 0%,transparent 80%),radial-gradient(ellipse 18% 40% at 68% 45%,#121212 0%,#b0242a 45%,transparent 80%),radial-gradient(ellipse 22% 18% at 40% 78%,#2d2d2d 0%,transparent 80%),#fff}
.tile-rebreather{background:radial-gradient(ellipse 30% 45% at 72% 55%,#1c1c1e 0%,#3a3b3e 55%,transparent 80%),radial-gradient(ellipse 22% 32% at 22% 68%,#dfe3e6 0%,#a6b3bc 55%,transparent 85%),#fff}
.tile-regulators{background:radial-gradient(ellipse 20% 20% at 75% 18%,#c6c9cc 0%,transparent 85%),radial-gradient(ellipse 35% 30% at 45% 65%,#2a2a2c 0%,#8e9297 55%,transparent 80%),#fff}
.tile-misc{background:radial-gradient(ellipse 28% 48% at 18% 50%,#f26a1b 0%,#f59150 55%,transparent 80%),radial-gradient(ellipse 18% 20% at 70% 18%,#4d4f52 0%,transparent 85%),radial-gradient(ellipse 22% 20% at 68% 78%,#2b6bc4 0%,#e6702a 55%,transparent 85%),#fff}
.trip{position:absolute;left:10px;width:176px;font-size:10px;line-height:13.5px;color:var(--muted)}
.trip h3{font-size:11.5px;font-weight:700;color:var(--ink)}
.trip time{display:block;font-size:11.5px;color:var(--ink);margin-bottom:4px}
.trip p{padding-left:8px}
.copy{left:0;width:1200px;top:660px;text-align:center;font-family:"Orbitron",sans-serif;font-size:10px;color:#fff;letter-spacing:.5px}
</style>
</head>
<body>
<div class="backdrop" role="img" aria-label="Underwater scene with a school of fish and technical rebreather divers"></div>

<div class="abs brand"><span class="brand-dot"></span><span class="brand-name">CREST<br>TIDE</span></div>

<div class="abs call">Questions?<br>Call us! 555.014.0277</div>
<div class="abs search"><span class="search-go">GO</span></div>

<nav class="abs topnav">
  <span>Home</span><span>About us</span><span>Send Email</span><span>Privacy Policy</span>
  <span><svg width="13" height="11" viewBox="0 0 13 11"><path d="M0 1h2.5l2 6h6l1.5-4.5H4" fill="none" stroke="#fff" stroke-width="1.3"/><circle cx="5.5" cy="9.5" r="1.2" fill="#fff"/><circle cx="9.5" cy="9.5" r="1.2" fill="#fff"/></svg>View Cart</span>
</nav>

<div class="abs ship"><b>FREE SHIPPING</b><small>In the Continental U.S.</small></div>
<div class="abs intl">Shipping International ?&nbsp;&nbsp;Click for details »</div>

<nav class="abs tabbar"><span>BEST SELLERS</span><span>NEW ARRIVALS</span><span>SALE</span></nav>

<main class="abs panel">
  <section class="col-side col-left">
    <h2 class="head" style="left:4px;width:182px">LEARN</h2>
    <article class="story" style="top:52px">
      <h3>Clearasept disinfectant</h3>
      <div class="photo photo-video" role="img" aria-label="Video still of a staff member presenting the disinfectant in the workshop"></div>
      <p>Crest Tide's Marla Venn speaks about our new disinfectant product.</p>
      <a class="more">Watch Video</a>
    </article>
    <article class="story" style="top:244px">
      <h3>Ready to pick your rebreather?</h3>
      <div class="photo photo-shop" style="height:112px" role="img" aria-label="Instructor seated beside rebreather units in the shop"></div>
      <p>Dean Harlow is certified to dive or instruct and sell over 8 different types of units. Read our articles to get unbiased reviews, tips and tricks from a group that doesn't have an agenda!</p>
      <a class="more">Read More...</a>
    </article>
  </section>

  <section>
    <h2 class="head" style="left:316px;width:181px">SHOP</h2>
    <div class="product" style="left:212px;top:58px"><div class="product-img tile-wings" role="img" aria-label="Black backplate and red wing harness"></div><p class="product-name">Backplates/Wings</p></div>
    <div class="product" style="left:354px;top:58px"><div class="product-img tile-computers" role="img" aria-label="Dive computers with colour screens"></div><p class="product-name">Electronics</p></div>
    <div class="product" style="left:492px;top:58px"><div class="product-img tile-handsets" role="img" aria-label="Handset, pouch and orange oxygen cylinder"></div><p class="product-name">Electronics</p></div>
    <div class="product" style="left:212px;top:214px"><div class="product-img tile-cylinders" role="img" aria-label="Steel cylinders and a black stage bottle"></div><p class="product-name">Exposure Protection</p></div>
    <div class="product" style="left:354px;top:214px"><div class="product-img tile-hardware" role="img" aria-label="Steel plate, bolt snap and o-rings"></div><p class="product-name">Hardware</p></div>
    <div class="product" style="left:492px;top:214px"><div class="product-img tile-lights" role="img" aria-label="Dive torches and battery canister"></div><p class="product-name">Lights</p></div>
    <div class="product" style="left:212px;top:375px"><div class="product-img tile-rebreather" role="img" aria-label="Rebreather unit and sorb container"></div><p class="product-name">Rebreathers</p></div>
    <div class="product" style="left:354px;top:375px"><div class="product-img tile-regulators" role="img" aria-label="Regulators, hoses and pressure gauge"></div><p class="product-name">Regulators</p></div>
    <div class="product" style="left:492px;top:375px"><div class="product-img tile-misc" role="img" aria-label="Orange lift bag, compass and line reel"></div><p class="product-name">Other Shit</p></div>
  </section>

  <section class="col-side col-right">
    <h2 class="head" style="left:6px;width:184px">DIVE</h2>
    <article class="trip" style="top:52px">
      <h3>Deepgather 2012!</h3><time>May 26-June 2, 2012</time>
      <p>Join Dean, Rob and Lena along with over 60 other CCR divers for a great week of diving Grand Cayman's deep walls.</p>
      <a class="more">Read More...</a>
    </article>
    <article class="trip" style="top:183px">
      <h3>Truk Lagoon CCR Trip</h3><time>July 13-July 23, 2012</time>
      <p>Dean and Marla make another trip out to dive the deep wrecks of Truk. Let Crest Tide make your trip easy by taking care</p>
      <a class="more">Read More...</a>
    </article>
    <article class="trip" style="top:312px">
      <h3>Dive with Team Crest Tide!</h3><time>Anytime</time>
      <p>The staff and friends of Crest Tide are out in the water every week diving South Florida's finest deep wrecks. Come join us!</p>
      <a class="more">Read More...</a>
    </article>
  </section>
</main>

<footer class="abs copy">copyright @ 2012</footer>
</body>
</html>
```